Medical Prescription for Diagnostic Sleep Testing

Quiet Harbor Rest Diagnostics main marketing tool is our Prescription that we leave with medical providers. Prescription is printed on 8.5 x 11 sheets of paper to create a prescription pad for our medical providers. Prescription should fit to one page. Quiet Harbor Rest Diagnostics works with 250 different medical providers so it is important we are able to update and change the medical provider information at bottom. The medical provider would fill-out top with patient information, check-off center testing and patient co-morbidity and Fax to Quiet Harbor Rest Diagnostics. Because it is Faxed to us it is important to have clear print and large font Attached or uploaded file is one example we currently use. Please review all 5 must haves.

Target Market(s)

Prescription for medical providers to fill-out and fax to Quiet Harbor Rest Diagnostics to conduct the sleep study.

Industry/Entity Type

Medical

Colors

Designer to choose only greyscale colors for use in the design.

Requirements
Must have
• 1) Prescription Size: 8.5 x 11
• 2) Must fit to One page Only
• 3) Ability to change medical provider information at bottom of prescription. We work with 250 different medical providers
• 4) Ability to change or update any part of prescription
• 5) Document Must be created in Microsoft Word 2016. This is the program we use for our prescriptions.
Nice to have
• Can be done in Gray-Scale or Black and White since its being faxed from the medical provider to us.

```html
<!DOCTYPE html>
<html lang="en">
<head>
<meta charset="utf-8">
<title>Sleep Study Physician Order</title>
<link href="https://fonts.googleapis.com/css2?family=Montserrat:wght@700;800&family=Roboto:ital,wght@0,400;0,700;1,400;1,700&family=Roboto+Condensed:ital,wght@1,700&display=swap" rel="stylesheet">
<style>
:root{
  --purple:#5c2a92;
  --purple-band:#6a2fa3;
  --ink:#1b1b1f;
  --muted:#2e2e34;
  --paper:#ffffff;
  --backdrop:#e7e6ea;
  --panel:#e4e3e7;
  --black-band:#111114;
}
*{box-sizing:border-box;margin:0;padding:0}
html,body{width:1180px;height:1200px;overflow:hidden}
body{background:var(--backdrop);font-family:"Roboto",Arial,sans-serif;color:var(--ink)}
.page{position:absolute;left:140px;top:18px;width:900px;height:1164px;background:var(--paper);box-shadow:0 2px 10px rgba(0,0,0,.12)}
.abs{position:absolute}
.title{left:34px;top:36px;font-family:"Montserrat",sans-serif;font-weight:800;font-size:32px;color:var(--purple);letter-spacing:.3px}
.contact{left:34px;top:80px;font-style:italic;font-size:17px;line-height:23px;color:var(--muted)}
.brand{left:690px;top:40px;width:176px;display:flex;align-items:center;gap:8px}
.brand-mark{width:16px;height:16px;background:var(--purple);flex:none}
.brand-name{font-family:"Montserrat",sans-serif;font-weight:700;font-size:17px;line-height:21px;color:var(--purple)}
.field-row{left:38px;width:830px;display:flex;align-items:flex-end;font-weight:700;font-size:15px;white-space:nowrap}
.line{border-bottom:1.3px solid var(--ink);height:14px;margin:0 4px}
.band{left:32px;width:840px;height:30px;border-radius:3px;color:#fff;font-family:"Montserrat",sans-serif;font-weight:700;font-size:18px;letter-spacing:.5px;padding:4px 0 0 18px}
.band.purple{background:var(--purple-band)}
.band.black{background:var(--black-band)}
.box{display:inline-block;width:17px;height:17px;border:2px solid var(--purple);border-radius:3px;flex:none}
.study{left:40px;width:830px;display:flex;gap:12px;font-size:14.5px;line-height:17px}
.study b{font-weight:700}
.note{font-style:italic;font-size:12.5px;font-weight:400}
.indent{padding-left:34px}
.necessity{left:52px;top:700px;width:800px;display:grid;grid-template-columns:314px 268px 1fr}
.necessity ul{list-style:none}
.necessity li{display:flex;align-items:center;gap:9px;font-style:italic;font-size:14.5px;height:19.7px}
.necessity .box{width:13px;height:13px;border-width:1.5px;border-radius:2px}
.clinic{left:28px;top:886px;width:844px;height:43px;background:var(--purple-band);border-radius:4px;color:#fff;display:flex;align-items:center;justify-content:space-between;padding:0 28px}
.clinic-name{font-family:"Montserrat",sans-serif;font-weight:700;font-size:23px;letter-spacing:.6px}
.clinic-info{font-style:italic;font-weight:700;font-size:11px;line-height:17px}
.providers{left:52px;top:936px;width:820px;display:grid;grid-template-columns:286px 270px 1fr;row-gap:10px}
.provider{display:flex;gap:12px}
.provider .box{width:18px;height:18px;margin-top:2px}
.provider-name{font-weight:700;font-size:16px;line-height:18px}
.provider-npi{font-weight:700;font-size:14px;line-height:16px}
.sign-panel{left:26px;top:1031px;width:848px;height:70px;background:var(--panel);border-radius:8px}
.sign-row{left:44px;top:1044px;width:810px;display:flex;align-items:flex-end;font-weight:700;font-size:15px;color:var(--purple)}
.sign-row .line{border-color:var(--ink)}
.fax-line{left:0;top:1074px;width:900px;text-align:center;font-style:italic;font-weight:700;font-size:15.5px}
.fax-line span{color:var(--purple)}
.thanks{left:0;top:1111px;width:900px;text-align:center;font-family:"Roboto Condensed",sans-serif;font-style:italic;font-weight:700;font-size:27px;color:var(--purple)}
.footer-note{left:38px;top:1144px;display:flex;align-items:center;gap:11px;font-style:italic;font-weight:700;font-size:15.5px}
.footer-note .sq{width:14px;height:14px;background:var(--purple)}
</style>
</head>
<body>
<main class="page">
  <h1 class="abs title">SLEEP STUDY PHYSICIAN ORDER</h1>
  <p class="abs contact">Phone: (555) 210-4471 &nbsp;•&nbsp; Fax: (555) 210-4480<br>2840 W. Lantern Avenue, Suite 7 - C; Bayview, NV 89501</p>
  <div class="abs brand"><span class="brand-mark"></span><span class="brand-name">Quiet Harbor Rest Diagnostics</span></div>

  <div class="abs field-row" style="top:156px">Patient Name:<span class="line" style="width:410px"></span>DOB:<span class="line" style="width:72px"></span>/<span class="line" style="width:72px"></span>/<span class="line" style="width:82px"></span></div>
  <div class="abs field-row" style="top:194px">Telephone:<span class="line" style="width:268px"></span>Alternate Telephone:<span class="line" style="width:282px"></span></div>
  <div class="abs field-row" style="top:233px">Primary Insurance:<span class="line" style="width:212px"></span>&nbsp;Secondary Insurance:<span class="line" style="width:268px"></span></div>
  <div class="abs field-row" style="top:271px">Height:<span class="line" style="width:218px"></span>Weight:<span class="line" style="width:196px"></span>Patient Gender (circle one): &nbsp; M &nbsp;/ &nbsp;F</div>

  <div class="abs band purple" style="top:322px">DIAGNOSTIC SLEEP STUDY ORDERED</div>

  <div class="abs study" style="top:384px"><span class="box"></span><div><b>COMPLETE SLEEP STUDY:</b> <span class="note" style="text-decoration:underline">(Based on Insurance or Patient's Choice)</span><br><span class="indent"><b>In-Lab Sleep Study (PSG) or Home Sleep Study</b> <span class="note">(PSG 95810 / HST 95806)</span></span><br><span style="padding-left:32px"><b>with follow-up PAP Titration Study</b> <span class="note">(PAP 95811 if positive for sleep apnea)</span></span></div></div>
  <div class="abs study" style="top:449px"><span class="box"></span><div><b>PEDIATRIC SLEEP STUDY: PSG w/End Tidal CO2 Monitoring</b><br><span class="note indent">(PSG 95782 under 6 years of age &amp; PSG 95810 older than 6 years of age)</span></div></div>
  <div class="abs study" style="top:501px"><span class="box"></span><div><b>In-Lab Diagnostic Sleep Study/Polysomnogram</b> <span class="note">(PSG 95810)</span></div></div>
  <div class="abs study" style="top:535px"><span class="box"></span><div><b>SPLIT-NIGHT STUDY</b> <span class="note">(PSG with PAP 95810 &amp; 95811)</span><br><span class="note indent"><b style="text-decoration:underline">To Comply with Accreditation &amp; Insurance Guidelines</b>: HI must be 20 or &nbsp; greater with minimum 2 hour recorded sleep time</span><br><span class="note">and 3 hours minimum to complete PAP treatment.</span></div></div>
  <div class="abs study" style="top:605px"><span class="box"></span><div><b>CPAP / BiPAP / BiPAP ST Titration Study</b> <span class="note">(Patients with documented sleep apnea 95811)</span></div></div>
  <div class="abs study" style="top:640px"><span class="box"></span><div><b>Home Sleep Study</b> <span class="note">(HST 95806 Conducted in patient's home &amp; unattended by technologist) (No insurance patient cost $250.00)</span></div></div>

  <div class="abs band black" style="top:669px">PATIENT MEDICAL NECESSITY – PLEASE CHECK ALL BOXES</div>

  <div class="abs necessity">
    <ul>
      <li><span class="box"></span>Atrial Fibrillation</li>
      <li><span class="box"></span>Bipolar Disorder</li>
      <li><span class="box"></span>Congestive Heart Failure</li>
      <li><span class="box"></span>COPD</li>
      <li><span class="box"></span>Depression</li>
      <li><span class="box"></span>Excessive Daytime Sleepiness</li>
      <li><span class="box"></span>Gasping Sensations with Frequent</li>
      <li><span class="box"></span>Awakenings</li>
      <li><span class="box"></span>Frequent Urination</li>
    </ul>
    <ul>
      <li><span class="box"></span>Heart Disease</li>
      <li><span class="box"></span>History Heart Attack</li>
      <li><span class="box"></span>Hypertension</li>
      <li><span class="box"></span>Insomnia</li>
      <li><span class="box"></span>Mental or Mood Disorder</li>
      <li><span class="box"></span>Loud Snoring</li>
      <li><span class="box"></span>Morbid Obesity / Obesity</li>
      <li><span class="box"></span>Morning Headaches</li>
      <li><span class="box"></span>Narcolepsy</li>
    </ul>
    <ul>
      <li><span class="box"></span>Opioid Use</li>
      <li><span class="box"></span>PTSD</li>
      <li><span class="box"></span>Pulmonary Disease</li>
      <li><span class="box"></span>Restless Leg Syndrome</li>
      <li><span class="box"></span>Seizures</li>
      <li><span class="box"></span>Shift Work Sleep disorder</li>
      <li><span class="box"></span>Stroke / TIA</li>
      <li><span class="box"></span>Witnessed Apnea</li>
      <li><span class="box"></span>Other: ______________</li>
    </ul>
  </div>

  <div class="abs clinic">
    <span class="clinic-name">SILVER RIDGE ENT + AIRWAY CLINIC</span>
    <span class="clinic-info">4150 N. Meadow Lane; Bayview, NV 89502-1160<br>Telephone: 555-318-2290 Fax: 555-318-2295</span>
  </div>

  <div class="abs providers">
    <div class="provider"><span class="box"></span><div><div class="provider-name">Dr. Elliot James Marren</div><div class="provider-npi">NPI: 1408836215</div></div></div>
    <div class="provider"><span class="box"></span><div><div class="provider-name">Dr. Paul R. Whitcomb</div><div class="provider-npi">NPI: 1537720948</div></div></div>
    <div class="provider"><span class="box"></span><div><div class="provider-name">Dr Howard L. Pemberton</div><div class="provider-npi">NPI: 1762204389</div></div></div>
    <div class="provider"><span class="box"></span><div><div class="provider-name">Dr. Nora Lindqvist</div><div class="provider-npi">NPI: 1845530926</div></div></div>
    <div class="provider"><span class="box"></span><div><div class="provider-name">Leah Brannigan, FNP-C</div><div class="provider-npi">NPI: 1973318504</div></div></div>
    <div class="provider"><span class="box"></span><div><div class="provider-name">Owen Tulley, PA-C</div><div class="provider-npi">NPI: 1629045713</div></div></div>
  </div>

  <div class="abs sign-panel"></div>
  <div class="abs sign-row">Physician's Signature:<span class="line" style="width:412px"></span>Date:<span class="line" style="width:44px"></span><span style="color:var(--ink)">/</span><span class="line" style="width:44px"></span><span style="color:var(--ink)">/</span><span class="line" style="width:50px"></span></div>
  <p class="abs fax-line"><span>Please Fax:</span> 555-210-4480 or <span>Email:</span> quietharborrest@mailbox.example</p>

  <p class="abs thanks">Thank You for Your Support GLENN &amp; MILO</p>
  <p class="abs footer-note"><span class="sq"></span>Fax Along With: Patient Demographic Information &nbsp;• Copy of Current Insurance Information &nbsp;• Clinical Notes</p>
</main>
</body>
</html>
```